Stonebridge Building and Projects business cards

A business card with watermark background (construction work)

Company logo attached

Home improvement projects
House renovations
Bathroom and kitchen renovations
House extensions
New builds and granny flats

Director Omar Haddani
(Phone number)
omar@sbpbuilding.com.au
(Instagram logo) sbp_building

```html
<!DOCTYPE html>
<html lang="en">
<head>
<meta charset="utf-8">
<title>Stonebridge Building and Projects – Business Card</title>
<link rel="stylesheet" href="https://fonts.googleapis.com/css2?family=Roboto:wght@400;500;700&display=swap">
<style>
  :root {
    --backdrop: #e9e4de;
    --card-frost: #f4f4f3;
    --card-frost-edge: #dcdcdb;
    --panel-blue: #1f6e98;
    --panel-blue-deep: #155a80;
    --panel-rim: #3b3f44;
    --name-blue: #1d6fa8;
    --ink: #3a3d40;
    --icon-ink: #2c4a63;
    --logo-sand: #e3d9cc;
  }
  * { box-sizing: border-box; margin: 0; padding: 0; }
  html, body {
    width: 1200px; height: 1054px; overflow: hidden;
    background: var(--backdrop);
    font-family: "Roboto", Arial, sans-serif;
  }
  .business-card {
    position: absolute;
    left: 100px; top: 224px;
    width: 1000px; height: 605px;
    border-radius: 30px;
    overflow: hidden;
    background: linear-gradient(135deg, #fafafa 0%, var(--card-frost) 55%, var(--card-frost-edge) 100%);
    box-shadow: 0 18px 40px rgba(60, 50, 40, 0.18);
  }
  .brand-panel { position: absolute; inset: 0; width: 1000px; height: 605px; }
  .contact-block { position: absolute; left: 47px; top: 166px; }
  .person-name { font-size: 36px; font-weight: 500; color: var(--name-blue); letter-spacing: 0.2px; }
  .person-role { margin-top: 10px; font-size: 25px; color: var(--ink); }
  .contact-list { list-style: none; margin-top: 40px; }
  .contact-item {
    display: flex; align-items: center; gap: 22px;
    height: 39px; font-size: 25px; color: var(--ink);
  }
  .contact-icon { width: 26px; height: 26px; flex: none; }
  .company-lockup {
    position: absolute; left: 600px; top: 232px; width: 360px;
    text-align: center; color: var(--logo-sand); font-weight: 500;
  }
  .company-mark {
    width: 70px; height: 70px; margin: 0 auto 18px;
    border: 4px solid var(--logo-sand);
  }
  .company-name-main { font-size: 40px; line-height: 1.1; }
  .company-name-sub {
    display: flex; align-items: center; gap: 12px;
    margin-top: 6px; font-size: 22px; white-space: nowrap;
  }
  .company-name-sub::before, .company-name-sub::after {
    content: ""; flex: 1; height: 2px; background: var(--logo-sand);
  }
</style>
</head>
<body>
  <div class="business-card">
    <svg class="brand-panel" viewBox="0 0 1000 605" aria-hidden="true">
      <defs>
        <linearGradient id="panelFill" x1="0" y1="0" x2="1" y2="1">
          <stop offset="0" stop-color="var(--panel-blue)"/>
          <stop offset="1" stop-color="var(--panel-blue-deep)"/>
        </linearGradient>
      </defs>
      <path d="M582 0 C520 120 490 330 520 460 C535 530 560 580 574 605 L1000 605 L1000 0 Z" fill="var(--panel-rim)"/>
      <path d="M596 0 C536 120 508 330 538 460 C552 530 576 580 590 605 L1000 605 L1000 0 Z" fill="url(#panelFill)"/>
    </svg>

    <div class="contact-block">
      <h1 class="person-name">Omar Haddani</h1>
      <p class="person-role">Managing Director</p>
      <ul class="contact-list">
        <li class="contact-item">
          <svg class="contact-icon" viewBox="0 0 26 26"><circle cx="13" cy="13" r="11" fill="none" stroke="var(--icon-ink)" stroke-width="2"/><path d="M9 7.5l2 2.5-1.3 1.5c.8 1.8 2 3 3.8 3.8l1.5-1.3 2.5 2-1.2 1.8c-4.5-.3-8.6-4.4-8.9-8.9z" fill="var(--icon-ink)"/></svg>
          0400 318 762
        </li>
        <li class="contact-item">
          <svg class="contact-icon" viewBox="0 0 26 26"><rect x="3" y="6" width="20" height="14" fill="none" stroke="var(--icon-ink)" stroke-width="2"/><path d="M3 6l10 8 10-8" fill="none" stroke="var(--icon-ink)" stroke-width="2"/></svg>
          omar@sbpbuilding.com.au
        </li>
        <li class="contact-item">
          <svg class="contact-icon" viewBox="0 0 26 26" fill="none" stroke="var(--icon-ink)" stroke-width="1.8"><circle cx="13" cy="13" r="10"/><ellipse cx="13" cy="13" rx="4.5" ry="10"/><path d="M3 13h20M5 8h16M5 18h16"/></svg>
          sbpbuilding.com.au
        </li>
        <li class="contact-item">
          <svg class="contact-icon" viewBox="0 0 26 26"><circle cx="13" cy="13" r="9" fill="none" stroke="var(--icon-ink)" stroke-width="2"/></svg>
          sbp_building
        </li>
      </ul>
    </div>

    <div class="company-lockup">
      <div class="company-mark"></div>
      <p class="company-name-main">Stonebridge</p>
      <p class="company-name-sub">Building and Projects</p>
    </div>
  </div>
</body>
</html>
```